Ledgerwise Forge - WordPress Theme & Logo

Design a logo and Wordpress website design for Ledgerwise Forge. Ledgerwise Forge provides cryptocurrency development services to clients who need a team to create & continue developing a new cryptocurrency or who want to replace their current cryptocurrency development team. more details in the attached document.
Updates

Target Market(s)

Entrepreneurs who are building a business / platform that makes use of an underlying cryptocurrency.

Logo Text

LF or Ledgerwise Forge

Coding

Coded - Design and coding required

Font styles to use
Sans Serif

Requirements
Must have
• Professional logo, complete coded Wordpress theme for all pages, containing all specified links and buttons
Nice to have
• It would be nice if the buttons that are meant to integrate with Dealtrail contain the necessary code for that. I can provide any necessary Dealtrail details from my account.
Should not have
• Slow loading time

```html
<!DOCTYPE html>
<html lang="en">
<head>
<meta charset="utf-8">
<title>Ledgerwise Forge – Your Own Cryptocurrency</title>
<link href="https://fonts.googleapis.com/css2?family=Roboto:ital,wght@0,400;0,500;0,700;1,400&display=swap" rel="stylesheet">
<style>
:root{
  --ink:#222222;
  --text:#555555;
  --muted:#777777;
  --teal:#2ecfcc;
  --green:#12b05a;
  --dark:#2b2b2b;
  --soft:#f6f6f6;
  --white:#ffffff;
  --line:#d9d9d9;
}
*{box-sizing:border-box;margin:0;padding:0}
html,body{width:1200px;height:4044px;overflow:hidden}
body{font-family:"Roboto",Arial,sans-serif;color:var(--ink);background:var(--white);position:relative}
section,header,footer{position:absolute;left:0;width:1200px}
.abs{position:absolute}

/* header + hero */
.hero{top:0;height:635px;background:linear-gradient(135deg,#ffffff 0%,#f4f4f4 60%,#ffffff 100%)}
.brand{left:110px;top:34px;font-size:21px;font-weight:700;letter-spacing:1px;color:var(--ink)}
.nav{left:466px;top:40px;display:flex;gap:26px;font-size:13px;font-weight:500;color:var(--ink);letter-spacing:.2px;list-style:none}
.nav .home{width:14px;height:14px}
.hero-title{left:110px;top:196px;font-size:42px;line-height:44px;font-weight:700;letter-spacing:.5px}
.hero-sub{left:110px;top:293px;font-size:21px;line-height:30px;font-weight:500;letter-spacing:.5px}
.btn{display:inline-flex;align-items:center;justify-content:center;font-size:13px;font-weight:700;letter-spacing:.3px;border-radius:4px;text-transform:uppercase}
.btn-outline-dark{left:111px;top:367px;width:202px;height:43px;border:2px solid var(--ink);color:var(--ink)}
.btn-teal{left:323px;top:367px;width:260px;height:43px;background:var(--teal);color:var(--white)}
.hero-art{left:610px;top:133px;width:490px;height:420px;border-radius:20px;background:radial-gradient(circle at 40% 45%,#3b7bff 0%,#73e3e0 45%,rgba(255,255,255,0) 72%)}

/* welcome */
.welcome{top:635px;height:339px;background:var(--dark);color:var(--white);text-align:center}
.welcome .kicker{margin-top:98px;font-size:17px;letter-spacing:6px;font-weight:500}
.welcome h2{margin-top:12px;font-size:33px;font-weight:700;letter-spacing:.5px}
.welcome p{width:720px;margin:14px auto 0;font-size:13.5px;line-height:22px}

/* why */
.why{top:974px;height:558px;text-align:center}
.why h2{margin-top:95px;font-size:34px;font-weight:700;letter-spacing:.5px}
.feature{width:220px;text-align:center}
.feature .icon{width:78px;height:78px;border-radius:50%;background:var(--teal);margin:0 auto;display:flex;align-items:center;justify-content:center}
.feature .dot{width:18px;height:18px;border-radius:50%;background:var(--ink);border:4px solid var(--teal);box-shadow:0 0 0 2px var(--ink);margin:13px auto 0}
.feature h3{font-size:19px;font-weight:500;margin-top:14px}
.feature p{font-size:13px;line-height:22px;color:var(--text);margin-top:6px}

/* who */
.who{top:1532px;height:510px;background:var(--soft)}
.who-box{left:0;top:78px;width:660px;height:303px;background:var(--teal);border-radius:0 6px 0 0}
.who h2{left:127px;top:150px;font-size:33px;font-weight:500;color:var(--white);letter-spacing:.5px}
.who p{left:127px;top:208px;width:450px;font-size:13px;line-height:22.5px;color:var(--white);text-align:justify}
.who-video{left:600px;top:128px;width:489px;height:305px;border-radius:6px;background:linear-gradient(135deg,#1f2e33 0%,#56707a 45%,#2a3a40 100%)}
.play{left:818px;top:255px;width:52px;height:52px;border-radius:50%;background:rgba(255,255,255,.9);display:flex;align-items:center;justify-content:center}

/* testimonials */
.testimonials{top:2042px;height:613px;text-align:center}
.testimonials h2{margin-top:95px;font-size:34px;font-weight:700;letter-spacing:.5px}
.quote-card{left:294px;top:160px;width:611px;height:308px;background:var(--white);box-shadow:0 2px 10px rgba(0,0,0,.12);border-radius:4px;text-align:center}
.stars{margin-top:20px;color:#f5b400;font-size:16px;letter-spacing:2px}
.quote-card h3{margin-top:8px;font-size:19px;font-weight:500}
.quote-card blockquote{width:520px;margin:10px auto 0;font-size:13px;line-height:22.5px;font-style:italic;color:var(--text)}
.quote-card cite{display:block;margin-top:6px;font-style:normal;font-size:18px;color:var(--ink)}
.avatar{border-radius:50%;border:3px solid #e6e6e6;background:linear-gradient(160deg,#b8cbd6,#5b7587)}
.arrow{font-size:20px;color:var(--ink)}

/* services */
.services{top:2655px;height:652px;background:var(--soft);text-align:center}
.services h2{margin-top:97px;font-size:34px;font-weight:700;letter-spacing:.5px}
.card{top:160px;width:313px;height:387px;background:var(--white);border-radius:3px;box-shadow:0 2px 8px rgba(0,0,0,.08);text-align:center}
.card.featured{background:linear-gradient(135deg,var(--teal),var(--green));color:var(--white)}
.card .art{width:220px;height:150px;margin:18px auto 0;border-radius:10px;background:linear-gradient(135deg,#e9e6ff,#b4a8ff 55%,#f4f4f4)}
.card.featured .art{background:linear-gradient(135deg,rgba(255,255,255,.25),rgba(40,40,110,.45))}
.card h3{font-size:19px;font-weight:500;line-height:26px;margin-top:14px;min-height:52px}
.card p{width:240px;margin:14px auto 0;font-size:13px;line-height:26px;color:var(--text)}
.card.featured p{color:var(--white)}
.card .btn{margin-top:16px;width:148px;height:43px;background:linear-gradient(90deg,var(--teal),var(--green));color:var(--white)}
.card.featured .btn{background:transparent;border:2px solid var(--white)}

/* cta */
.cta{top:3307px;height:311px;background:linear-gradient(90deg,var(--teal),var(--green));text-align:center;color:var(--white)}
.cta h2{margin-top:72px;font-size:34px;font-weight:500;letter-spacing:1px}
.cta p{width:620px;margin:14px auto 0;font-size:13.5px;line-height:25px}
.cta .btn{margin-top:22px;width:258px;height:43px;border:2px solid var(--white);color:var(--white)}

/* footer */
.site-footer{top:3618px;height:426px}
.fcol{top:100px}
.fcol h4{font-size:18px;font-weight:500;text-decoration:underline;text-underline-offset:3px}
.fcol ul{list-style:none;margin-top:12px}
.fcol li{font-size:13px;line-height:22.5px;color:var(--text)}
.fcol li::before{content:"»";margin-right:9px;color:var(--muted)}
.f-brand{left:110px;top:100px;width:180px}
.f-brand h4{font-size:18px;line-height:25px;font-weight:700;letter-spacing:.5px}
.f-brand p{font-size:13px;line-height:22px;color:var(--text);margin-top:6px}
.email{width:277px;height:44px;border:1px solid #cfcfcf;font-size:13px;color:var(--text);display:flex;align-items:center;padding-left:18px;margin-top:24px}
.submit{margin-top:17px;width:119px;height:43px;background:linear-gradient(90deg,var(--teal),var(--green));color:var(--white);font-size:13px;font-weight:700;display:flex;align-items:center;justify-content:center}
.copyright{left:0;width:1200px;top:378px;text-align:center;font-size:13px;color:var(--ink)}
</style>
</head>
<body>

<header class="hero">
  <div class="abs brand">LEDGERWISE FORGE</div>
  <ul class="abs nav">
    <li><svg class="home" viewBox="0 0 14 14"><path d="M7 1 1 6.5h2V13h3V9h2v4h3V6.5h2z" fill="#222"/></svg></li>
    <li>SERVICES</li>
    <li>LEDGERWISE FORGE METHOD</li>
    <li>TESTIMONIALS</li>
    <li>BLOG</li>
    <li>ABOUT US</li>
  </ul>
  <h1 class="abs hero-title">YOUR OWN<br>CRYPTOCURRENCY.</h1>
  <div class="abs hero-sub">SECURE, EASY TO USE, AND BUILT<br>BY AN EXPERT TEAM.</div>
  <a class="abs btn btn-outline-dark">Download a free PDF</a>
  <a class="abs btn btn-teal">Schedule free consultation</a>
  <div class="abs hero-art" role="img" aria-label="Isometric illustration of server racks and two people reviewing data charts on a large screen"></div>
</header>

<section class="welcome">
  <div class="kicker">WELCOME TO</div>
  <h2>LEDGERWISE FORGE</h2>
  <p>Ledgerwise Forge adds professionalism to cryptocurrency development. Our done-for-you service covers everything from development and IT operations to ongoing support. You have access to a full team, for less than the typical cost of a single developer.</p>
</section>

<section class="why">
  <h2>WHY CHOOSE LEDGERWISE FORGE</h2>
  <svg class="abs" style="left:0;top:0" width="1200" height="558" viewBox="0 0 1200 558">
    <path d="M170 312 C 240 270, 280 262, 314 262 C 420 262, 520 290, 600 313 C 700 342, 790 363, 886 363 C 950 363, 990 340, 1029 312" fill="none" stroke="#333" stroke-width="1.5"/>
  </svg>
  <div class="abs feature" style="left:204px;top:158px">
    <div class="icon"><svg width="40" height="40" viewBox="0 0 40 40" fill="none" stroke="#fff" stroke-width="2"><path d="M6 15 12 7h16l6 8-14 18z"/><path d="M6 15h28M15 15l5 18 5-18M12 7l3 8 5-8 5 8 3-8"/></svg></div>
    <div class="dot"></div>
    <h3>Value</h3>
    <p>A team of experts, regular<br>updates, and fixed costs</p>
  </div>
  <div class="abs feature" style="left:490px;top:208px">
    <div class="icon"><svg width="40" height="40" viewBox="0 0 40 40" fill="none" stroke="#fff" stroke-width="2"><path d="M8 26 17 17l5 4 4-4 6 6-8 8-6-3-4 4z"/><path d="M17 17l-4-4M26 17l4-4M20 6v4M13 8l2 3M27 8l-2 3"/></svg></div>
    <div class="dot"></div>
    <h3>Support</h3>
    <p>Receive advice and other<br>services, beyond<br>development.</p>
  </div>
  <div class="abs feature" style="left:776px;top:257px">
    <div class="icon"><svg width="40" height="40" viewBox="0 0 40 40" fill="none" stroke="#fff" stroke-width="2"><rect x="9" y="6" width="20" height="27" rx="2"/><path d="M13 13h12M13 18h12M13 23h6M24 30l8-10 3 2-8 10-4 1z"/></svg></div>
    <div class="dot"></div>
    <h3>Commitment</h3>
    <p>Enjoy regular updates and<br>new features.</p>
  </div>
</section>

<section class="who">
  <div class="abs who-box"></div>
  <h2 class="abs">WHO WE ARE</h2>
  <p class="abs">In addition to creating and enhancing cryptocurrencies for clients, the Ledgerwise Forge team has been running the Corvane cryptocurrency since 2017. We prefer long-term relationships, enabling us to deliver the very highest quality and giving you peace of mind that you've got a professional and trustworthy team at your side.</p>
  <div class="abs who-video" role="img" aria-label="Video still of a professional overlaid with a digital network of connected points"></div>
  <div class="abs play"><svg width="18" height="20" viewBox="0 0 18 20"><path d="M2 1 17 10 2 19z" fill="#2ecfcc"/></svg></div>
</section>

<section class="testimonials">
  <h2>CLIENT TESTIMONIALS</h2>
  <div class="abs arrow" style="left:168px;top:302px">&larr;</div>
  <div class="abs arrow" style="left:1012px;top:302px">&rarr;</div>
  <div class="abs quote-card">
    <div class="stars">★★★★★</div>
    <h3>Duis aute irure dolor in reprehenderit</h3>
    <blockquote>"Lorem ipsum dolor sit amet, consectetur adipiscing elit, sed do eiusmod tempor incididunt ut labore et dolore magna aliqua. Ut enim ad minim veniam, quis nostrud exercitation ullam co laboris nisi ut aliquip ex ea commodo consequat. Duis aute irure dolor in reprehenderit in voluptate velit esse cillum dolore eu fugiat nulla pariatur. Excepteur sint occaecat cupidatat non proident, sunt in culpa qui officia deserunt mollit anim id est laborum."</blockquote>
    <cite>Sam Ellery</cite>
  </div>
  <div class="abs avatar" role="img" aria-label="Client portrait" style="left:468px;top:430px;width:74px;height:74px"></div>
  <div class="abs avatar" role="img" aria-label="Client portrait, selected" style="left:556px;top:424px;width:86px;height:86px"></div>
  <div class="abs avatar" role="img" aria-label="Client portrait" style="left:656px;top:430px;width:74px;height:74px"></div>
</section>

<section class="services">
  <h2>OUR SERVICES</h2>
  <div class="abs card" style="left:110px">
    <div class="art" role="img" aria-label="Isometric illustration of a person building connected blockchain blocks"></div>
    <h3>Blockchain creation<br>and launch</h3>
    <p>Lorem ipsum dolor sit amet, conse ctetur adipiscing elit, sed do eiusmod tempor incididunt ut labore</p>
    <a class="btn">Learn more ➔</a>
  </div>
  <div class="abs card featured" style="left:443px">
    <div class="art" role="img" aria-label="Isometric illustration of a laptop surrounded by phones and code screens"></div>
    <h3>Basic</h3>
    <p>Lorem ipsum dolor sit amet, conse ctetur adipiscing elit, sed do eiusmod tempor incididunt ut labore</p>
    <a class="btn">Learn more ➔</a>
  </div>
  <div class="abs card" style="left:776px">
    <div class="art" role="img" aria-label="Isometric illustration of a developer working at a desk with floating charts"></div>
    <h3>Mid-range</h3>
    <p>Lorem ipsum dolor sit amet, conse ctetur adipiscing elit, sed do eiusmod tempor incididunt ut labore</p>
    <a class="btn">Learn more ➔</a>
  </div>
</section>

<section class="cta">
  <h2>SCHEDULE FREE CONSULTATION</h2>
  <p>Lorem ipsum dolor sit amet, consectetur adipiscing elit, sed do eiusmod tempor incididunt ut labore et dolore magna aliqua. Ut enim ad minim veniam, quis nostrud exercitation</p>
  <a class="btn">Schedule free consultation</a>
</section>

<footer class="site-footer">
  <div class="abs f-brand">
    <h4>LEDGERWISE<br>FORGE.</h4>
    <p>Lorem ipsum dolor sit amet, consectetur adipiscing elit, sed do eiusmod tempor incididunt ut labore et dolore magna aliqua. Ut enim ad minim veniam, quis</p>
  </div>
  <div class="abs fcol" style="left:346px">
    <h4>SITE CONTENT</h4>
    <ul><li>Consulting</li><li>Learning</li><li>Coding</li><li>Development</li><li>About Us</li><li>Contact Us</li><li>Careers – Job Opportunities</li><li>Sitemap</li></ul>
  </div>
  <div class="abs fcol" style="left:584px">
    <h4>QUICK LINKS</h4>
    <ul><li>Home</li><li>About us</li><li>Services</li><li>Ledgerwise Forge Method</li><li>Testimonials</li><li>Blog</li><li>Free Consultation</li><li>Contact us</li></ul>
  </div>
  <div class="abs fcol" style="left:812px">
    <h4>GET OUR NEWSLETTER</h4>
    <div class="email">Email address</div>
    <div class="submit">SUBMIT</div>
  </div>
  <div class="abs copyright">© 2021 Company name. All Rights Reserved</div>
</footer>

</body>
</html>
```